Brochure required

Looking at getting business brochure designed for my solar sales company. i will require a range of products to be listed on the brochure I require a simple/ elegent / professional looking brochure.

I am happy to provide designer with all the required information that must go into the brochure. otherwise please visit www.quillebartow.com.au and view the products which i would like to allocate into the brochure aswell as our company logo and a little about me section

```html
<!DOCTYPE html>
<html lang="en">
<head>
<meta charset="utf-8">
<title>Solar Services Brochure</title>
<link rel="stylesheet" href="https://fonts.googleapis.com/css2?family=Open+Sans:wght@300;700&display=swap">
<style>
  :root {
    --page-bg: #ffffff;
    --frame: #000000;
    --panel-deep: #1d3f73;
    --panel-mid: #2e5a93;
    --roof-grey: #9c9fa6;
    --roof-light: #c9ccd2;
    --accent-green: #00b386;
    --text-light: #ffffff;
  }
  html, body {
    margin: 0;
    padding: 0;
    width: 1200px;
    height: 1000px;
    overflow: hidden;
    background: var(--page-bg);
  }
  .canvas {
    position: relative;
    width: 1200px;
    height: 1000px;
  }
  .brochure-page {
    position: absolute;
    left: 257px;
    top: 14px;
    width: 681px;
    height: 968px;
    border: 3px solid var(--frame);
    background: var(--page-bg);
  }
  .hero-photo {
    position: absolute;
    left: 299px;
    top: 61px;
    width: 604px;
    height: 877px;
    background:
      linear-gradient(135deg,
        rgba(201,204,210,0.55) 0%,
        rgba(156,159,166,0.35) 28%,
        rgba(46,90,147,0) 48%),
      linear-gradient(160deg, var(--panel-mid) 0%, var(--panel-deep) 55%, #244a80 100%);
    overflow: hidden;
  }
  .corner-tab {
    position: absolute;
    left: 841px;
    top: 61px;
    width: 62px;
    height: 62px;
    background: var(--accent-green);
    border-radius: 4px 20px 0 4px;
  }
  .hero-copy {
    position: absolute;
    left: 341px;
    top: 540px;
    width: 395px;
    color: var(--text-light);
    font-family: "Open Sans", sans-serif;
  }
  .headline {
    margin: 0;
    font-weight: 700;
    font-size: 36px;
    line-height: 48.5px;
    letter-spacing: -0.2px;
  }
  .intro {
    margin: 30px 0 0;
    font-weight: 300;
    font-size: 16.5px;
    line-height: 21.5px;
    text-align: justify;
    letter-spacing: -0.3px;
  }
</style>
</head>
<body>
<div class="canvas">
  <div class="brochure-page"></div>
  <div class="hero-photo" role="img" aria-label="Aerial view of rows of blue solar panels on an industrial metal roof"></div>
  <div class="corner-tab"></div>
  <div class="hero-copy">
    <h1 class="headline">We pride ourselves<br>on providing<br>premium quality<br>solar services</h1>
    <p class="intro">Lorem ipsum dolor sit amet, consectetuer adipiscing elit, sed diam nonummy nibh euismod tincidunt ut laoreet dolore magna aliquam erat volutpat. Ut wisi enim ad minim veniam, quis nostrud exerci tation ullamcorper suscipit lobortis nisl ut aliquip ex ea commodo</p>
  </div>
</div>
</body>
</html>
```